Roofing company in Toronto, Canada needs a logo design and business card design

We need a business card and logo created for our company. Our company is "KLV Roofing" which provides roofing services for commercial and residential customers. We serve customers in the Greater Toronto Area (in Canada) thus the name KLV.

We want the logo and business card to be a modern design displaying professionalism and quality in the work. We would prefer rounded corners for the business cards but are open to other ideas. The cards should be pleasant and appealing to customers.

Target Market(s)

Commercial and Residential customers

Industry/Entity Type

Roofing

Contact Information for Business Card

Logo Text

KLV Roofing

Requirements
Nice to have
• Colours that are pleasing to the eye but at the same time should stand out from other business cards. If the design can incorporate the name of KLV Roofing and the actual concept of roofing that would be nice.
Should not have
• Do not want the business cards or logo to be childish looking. Need to look professionally designed.

```html
<!DOCTYPE html>
<html lang="en">
<head>
<meta charset="utf-8">
<title>KLV Roofing – Business Card</title>
<link href="https://fonts.googleapis.com/css2?family=Open+Sans:wght@400;600;700&display=swap" rel="stylesheet">
<style>
  :root {
    --backdrop: #2f2f2f;
    --card-white: #ffffff;
    --brand-blue: #1c74c9;
    --brand-blue-deep: #1a6cbd;
    --divider-grey: #8e8e8e;
    --text-grey: #4a4a4a;
    --text-white: #ffffff;
  }
  * { margin: 0; padding: 0; box-sizing: border-box; }
  html, body {
    width: 1200px; height: 900px; overflow: hidden;
    background: var(--backdrop);
    font-family: "Open Sans", Arial, sans-serif;
  }
  .stage { position: relative; width: 1200px; height: 900px; }
  .card {
    position: absolute; top: 306px;
    width: 440px; height: 271px;
    border-radius: 10px; overflow: hidden;
  }
  .card-front { left: 149px; background: var(--card-white); }
  .card-back { left: 608px; background: var(--brand-blue); }

  .front-band {
    position: absolute; left: 0; right: 0; top: 137px; bottom: 0;
    background: var(--brand-blue-deep);
    border-top: 6px solid var(--divider-grey);
  }
  .brand-name {
    font-weight: 700; letter-spacing: 0.5px; white-space: nowrap;
  }
  .front-brand {
    position: absolute; left: 24px; top: 46px;
    font-size: 36px; line-height: 1; color: var(--brand-blue);
  }
  .holder {
    position: absolute; right: 23px; top: 54px; text-align: right;
  }
  .holder-name {
    font-size: 14px; font-weight: 700; color: var(--brand-blue);
    text-transform: uppercase; line-height: 18px;
  }
  .holder-role { font-size: 12px; color: var(--text-grey); line-height: 16px; }

  .contact-list {
    position: absolute; left: 24px; top: 14px;
    list-style: none; color: var(--text-white); font-size: 12.5px;
  }
  .contact-list li { display: flex; align-items: center; height: 16px; }
  .contact-list svg { width: 9px; height: 9px; margin-right: 6px; fill: var(--text-white); }
  .address {
    position: absolute; left: 23px; top: 72px;
    color: var(--text-white); font-size: 12.5px; line-height: 17px;
  }

  .back-brand {
    position: absolute; left: 0; right: 0; top: 105px; text-align: center;
    font-size: 54px; line-height: 1; color: var(--text-white);
  }
  .back-web {
    position: absolute; left: 0; right: 0; top: 228px; text-align: center;
    font-size: 12px; color: var(--text-white);
  }
</style>
</head>
<body>
<main class="stage">
  <section class="card card-front">
    <div class="brand-name front-brand">KLV Roofing</div>
    <div class="holder">
      <div class="holder-name">Marcus Doyle</div>
      <div class="holder-role">Managing Director</div>
    </div>
    <div class="front-band">
      <ul class="contact-list">
        <li><svg viewBox="0 0 10 10"><path d="M2 0.5 L3.6 2.6 L2.8 3.6 Q4 6 6.4 7.2 L7.4 6.4 L9.5 8 L8.5 9.5 Q3.5 9 0.5 1.5 Z"/></svg>(044)987650321</li>
        <li><svg viewBox="0 0 10 10"><path d="M0.5 2 H9.5 V8 H0.5 Z M1 2.5 L5 5.5 L9 2.5" stroke="#1a6cbd" stroke-width="0.8"/></svg>hello@klvroofing.ca</li>
        <li><svg viewBox="0 0 10 10"><circle cx="5" cy="5" r="4.5"/><path d="M0.5 5 H9.5 M5 0.5 Q2.5 5 5 9.5 M5 0.5 Q7.5 5 5 9.5" stroke="#1a6cbd" stroke-width="0.7" fill="none"/></svg>www.klvroofing.ca</li>
      </ul>
      <p class="address">58, Harbour Lane,<br>Ontario, 40213</p>
    </div>
  </section>

  <section class="card card-back">
    <div class="brand-name back-brand">KLV Roofing</div>
    <div class="back-web">www.klvroofing.ca</div>
  </section>
</main>
</body>
</html>
```